Estate Planning Law Firm opening new branch in Florida

I am an experienced estate planning attorney that recently relocated to Florida. Looking for a banner Ad to place on platforms such as HomeLane, Chatterbox and Picturely to create publicity for firm and new leads.

```html
<!DOCTYPE html>
<html lang="en">
<head>
<meta charset="utf-8">
<title>Halcyon Law Firm – Welcome Banner</title>
<link rel="stylesheet" href="https://fonts.googleapis.com/css2?family=Cinzel:wght@700&family=Cormorant+SC:wght@700&family=Lora:wght@400&family=Poppins:wght@500&display=swap">
<style>
  :root {
    --navy: #2b3a4d;
    --ring-navy: #34557a;
    --teal: #1b6e6e;
    --teal-dark: #1c4f58;
    --teal-light: #9fd3d3;
    --body-grey: #6b6b6b;
    --bg: #fbfbfb;
    --white: #ffffff;
  }
  html, body {
    margin: 0;
    padding: 0;
    overflow: hidden;
    background: var(--bg);
  }
  .banner {
    position: relative;
    width: 1200px;
    height: 628px;
    overflow: hidden;
    background: var(--bg);
  }
  .decor {
    position: absolute;
    inset: 0;
  }
  .brand {
    position: absolute;
    left: 68px;
    top: 62px;
    display: flex;
    align-items: center;
    gap: 16px;
  }
  .brand-square {
    width: 44px;
    height: 44px;
    background: var(--teal);
  }
  .brand-name {
    font-family: "Cinzel", serif;
    font-weight: 700;
    font-size: 40px;
    letter-spacing: 1px;
    color: var(--navy);
    line-height: 1;
  }
  .headline {
    position: absolute;
    left: 68px;
    top: 205px;
    margin: 0;
    font-family: "Cinzel", serif;
    font-weight: 700;
    font-size: 64px;
    line-height: 72px;
    letter-spacing: 1px;
    color: var(--navy);
  }
  .cta {
    position: absolute;
    left: 68px;
    top: 374px;
    width: 322px;
    height: 46px;
  }
  .cta svg {
    position: absolute;
    inset: 0;
  }
  .cta-label {
    position: relative;
    display: block;
    text-align: center;
    line-height: 46px;
    font-family: "Cormorant SC", serif;
    font-weight: 700;
    font-size: 21px;
    letter-spacing: 0.5px;
    color: var(--white);
  }
  .intro {
    position: absolute;
    left: 68px;
    top: 448px;
    width: 430px;
    margin: 0;
    font-family: "Lora", serif;
    font-size: 17px;
    line-height: 26px;
    color: var(--body-grey);
  }
  .social {
    position: absolute;
    left: 68px;
    top: 581px;
    display: flex;
    gap: 22px;
    font-family: "Poppins", sans-serif;
    font-weight: 500;
    font-size: 10px;
    color: var(--navy);
  }
  .social-item {
    display: flex;
    align-items: center;
    gap: 6px;
  }
  .social-dot {
    width: 15px;
    height: 15px;
    border-radius: 50%;
    background: var(--teal);
  }
</style>
</head>
<body>
<main class="banner">
  <svg class="decor" width="1200" height="628" viewBox="0 0 1200 628">
    <defs>
      <linearGradient id="blobTop" x1="0" y1="0" x2="1" y2="1">
        <stop offset="0" stop-color="#d7efef"/>
        <stop offset="0.6" stop-color="#5fb0b0"/>
        <stop offset="1" stop-color="#1f6f72"/>
      </linearGradient>
      <linearGradient id="blobBottom" x1="0" y1="0" x2="1" y2="1">
        <stop offset="0" stop-color="#e4f4f4"/>
        <stop offset="1" stop-color="#8fcaca"/>
      </linearGradient>
      <linearGradient id="photoTone" x1="0" y1="0" x2="1" y2="1">
        <stop offset="0" stop-color="#b27a5e"/>
        <stop offset="0.45" stop-color="#8a6a5c"/>
        <stop offset="1" stop-color="#2c3548"/>
      </linearGradient>
    </defs>
    <!-- top right wave -->
    <path d="M700 0 C760 30 820 10 880 40 C940 70 980 30 1040 60 C1100 90 1120 120 1200 140 L1200 0 Z" fill="url(#blobTop)" opacity="0.55"/>
    <path d="M880 0 C930 40 990 20 1050 45 C1110 70 1150 110 1200 120 L1200 0 Z" fill="url(#blobTop)"/>
    <!-- bottom right wave -->
    <path d="M900 628 C950 560 1020 600 1080 540 C1120 500 1160 480 1200 470 L1200 628 Z" fill="url(#blobBottom)"/>
    <path d="M1000 628 C1050 590 1110 610 1200 560 L1200 628 Z" fill="#b9e0e0" opacity="0.8"/>
    <!-- teal arc behind frame -->
    <circle cx="882" cy="345" r="198" fill="none" stroke="var(--teal)" stroke-width="6"/>
    <!-- photo frame -->
    <circle cx="900" cy="325" r="200" fill="var(--white)" stroke="var(--ring-navy)" stroke-width="14"/>
    <circle cx="900" cy="325" r="190" fill="url(#photoTone)" role="img" aria-label="Portrait photo of the firm's two attorneys smiling in front of a brick wall"/>
    <!-- accent rings -->
    <circle cx="660" cy="158" r="16" fill="none" stroke="var(--teal)" stroke-width="6"/>
    <circle cx="1072" cy="200" r="30" fill="none" stroke="var(--teal)" stroke-width="7"/>
    <circle cx="752" cy="560" r="10" fill="none" stroke="var(--teal)" stroke-width="5"/>
  </svg>

  <div class="brand">
    <span class="brand-square"></span>
    <span class="brand-name">HALCYON LAW FIRM, PLLC</span>
  </div>

  <h1 class="headline">WELCOME TO<br>HALCYON</h1>

  <a class="cta">
    <svg width="322" height="46" viewBox="0 0 322 46">
      <defs>
        <linearGradient id="ctaFill" x1="0" y1="0" x2="1" y2="0">
          <stop offset="0" stop-color="var(--teal-dark)"/>
          <stop offset="1" stop-color="var(--teal)"/>
        </linearGradient>
      </defs>
      <path d="M30 0 H300 C314 0 322 10 322 23 L322 46 H0 V30 C0 12 12 0 30 0 Z" fill="url(#ctaFill)"/>
    </svg>
    <span class="cta-label">Book An Initial Call</span>
  </a>

  <p class="intro">Estate planning and financial planning isn’t just for the ultra-wealthy. We’re here to help families plan for their legacy and protect their wealth</p>

  <nav class="social">
    <span class="social-item"><span class="social-dot"></span>Picturely</span>
    <span class="social-item"><span class="social-dot"></span>Chatterbox</span>
    <span class="social-item"><span class="social-dot"></span>Chirpline</span>
  </nav>
</main>
</body>
</html>
```